Dalvick's Business Card

I need some designs for a new business card including the new logo attached. An old example of our business card is also attached to show all the data that should be included on the new design.
**I added some more examples someone had mocked up**

Contact Information for Business Card

Should include all info on other examples uploaded.

```html
<!DOCTYPE html>
<html lang="en">
<head>
<meta charset="utf-8">
<title>Dalvick's Business Card</title>
<link rel="stylesheet" href="https://fonts.googleapis.com/css2?family=Poppins:wght@400;600;700&display=swap">
<style>
  :root {
    --backdrop: #2a2a2b;
    --card: #1e1f21;
    --card-back: #111112;
    --blue: #0a6fc9;
    --red: #e8202a;
    --white: #f2f2f2;
  }
  * { box-sizing: border-box; margin: 0; padding: 0; }
  html, body { width: 1200px; height: 1108px; overflow: hidden; }
  body {
    background: var(--backdrop);
    font-family: 'Poppins', sans-serif;
    display: flex;
    align-items: center;
    justify-content: center;
    gap: 70px;
  }
  .card {
    width: 440px;
    height: 700px;
    border-radius: 22px;
    box-shadow: 0 18px 40px rgba(0,0,0,0.45);
  }
  .card-front {
    background: var(--card);
    display: flex;
    flex-direction: column;
    align-items: center;
    text-align: center;
    padding: 120px 30px 0;
  }
  .brand {
    display: flex;
    align-items: center;
    gap: 14px;
    margin-bottom: 90px;
  }
  .brand-dot {
    width: 38px; height: 38px;
    border-radius: 50%;
    background: var(--red);
  }
  .brand-name {
    color: var(--blue);
    font-weight: 600;
    font-size: 52px;
    letter-spacing: 1px;
    line-height: 1;
  }
  .person-name {
    color: var(--blue);
    font-weight: 700;
    font-size: 28px;
    text-transform: uppercase;
  }
  .rule {
    width: 150px;
    height: 2px;
    background: var(--blue);
    margin: 14px 0;
  }
  .contact { color: var(--white); font-size: 21px; line-height: 1.35; }
  .badge { font-weight: 700; font-size: 21px; text-transform: uppercase; line-height: 1.3; }
  .badge-blue { color: var(--blue); }
  .badge-red { color: var(--red); }
  .area { color: var(--white); font-size: 21px; line-height: 1.35; }
  .cta {
    color: var(--red);
    font-weight: 600;
    font-size: 20px;
    text-transform: uppercase;
    line-height: 1.35;
  }
  .card-back {
    position: relative;
    overflow: hidden;
    background: var(--card-back);
  }
  .back-pattern {
    position: absolute; inset: 0;
    background: linear-gradient(160deg, #3a3a3c 0%, #1a1a1b 45%, #0c0c0d 100%);
  }
  .back-mark {
    position: absolute;
    left: 50%; top: 60%;
    transform: translate(-50%, -50%);
    color: var(--blue);
    font-weight: 600;
    font-size: 24px;
  }
</style>
</head>
<body>
  <section class="card card-front">
    <div class="brand">
      <span class="brand-dot"></span>
      <span class="brand-name">DALVICK'S</span>
    </div>
    <p class="person-name">Grant Dalvick</p>
    <div class="rule"></div>
    <p class="contact">555.014.2290<br>hvacdalvick@mailbox.com</p>
    <div class="rule"></div>
    <p class="badge badge-blue">Licensed &amp; Insured</p>
    <p class="badge badge-red">Family Owned &amp; Operated</p>
    <div class="rule"></div>
    <p class="area">Serves Brookfield<br>IA &amp; Surrounding Areas</p>
    <div class="rule"></div>
    <p class="cta">Call today for all your HVAC<br>refrigeration &amp; plumbing needs</p>
  </section>
  <section class="card card-back">
    <div class="back-pattern" role="img" aria-label="Repeating glossy embossed pattern of the brand mark on black"></div>
    <span class="back-mark">Dalvick's</span>
  </section>
</body>
</html>
```